Dietitian needs awesome business card

I need a contemporary design that's eye catching but professional.
My card is to given to doctors, specialists and patients alike.
I manage patients with chronic diseases
I have uploaded my logo and current business card, I would also like the other Certified Clinical Nutritionist logo incorporated into the design

Target Market(s)

Doctors, specialists and patients

Industry/Entity Type

Healthcare

Contact Information for Business Card

www.brightfieldnutrition.com.au
Ph: 0427 561 903
Fax: 6457 2183
email: marcus.k.diet@fernmail.com
Space on the back of the card with: Appointment date, Appointment time and appointment location

Font styles to use
Serif

Colors
fbee3e
876aae
ffc214

Requirements
Must have
• My Logo
• Certified Clinical Nutritionist Logo
• My 4 locations - Pinebrook Medical Centre, North Corrin Health, Hollis Medical, Ashcombe Doctors Surgery
Nice to have
• I like the colours in my current business card

```html
<!DOCTYPE html>
<html lang="en">
<head>
<meta charset="utf-8">
<title>Brightfield – Business Card</title>
<link rel="stylesheet" href="https://fonts.googleapis.com/css2?family=Cabin:wght@400;500&family=Marcellus&family=Noto+Serif&display=swap">
<style>
  :root {
    --bg: #8c8c8c;
    --blue-deep: #1d2a8c;
    --blue-light: #0a78c8;
    --green: #8cc63f;
    --green-name: #a6d13a;
    --ink-blue: #2b3a8f;
    --white: #ffffff;
    --rule: #9a9a9a;
    --badge: #f47b20;
    --band-dark: #3f4a30;
    --band-light: #5c6a48;
    --accent-gold: #ffc214;
  }
  * { margin: 0; padding: 0; box-sizing: border-box; }
  html, body { width: 1105px; height: 1200px; overflow: hidden; }
  body { background: var(--bg); position: relative; font-family: "Cabin", sans-serif; }

  .card {
    position: absolute; left: 182px; width: 709px; height: 427px;
    overflow: hidden; background: var(--white);
  }
  .card--front { top: 119px; }
  .card--back { top: 637px; }

  .front-art { position: absolute; inset: 0; width: 100%; height: 100%; }

  .holder-name {
    position: absolute; left: 39px; top: 40px;
    font-family: "Marcellus", serif; font-size: 25px; font-weight: 400;
    letter-spacing: 0.5px; color: var(--green-name);
  }
  .holder-role {
    position: absolute; left: 39px; top: 76px;
    font-size: 19px; color: var(--white);
  }
  .contact-list {
    position: absolute; left: 39px; top: 276px; list-style: none;
    font-size: 19px; line-height: 28px; color: var(--white);
  }

  .brand {
    position: absolute; left: 400px; top: 190px;
    display: flex; align-items: center; gap: 12px;
  }
  .brand-dot { width: 48px; height: 48px; border-radius: 50%; background: var(--green); }
  .brand-name { font-size: 40px; color: var(--blue-deep); font-weight: 400; }

  .credential-badge {
    position: absolute; left: 119px; top: 60px; width: 178px; height: 84px;
    background: var(--badge); border-radius: 4px;
  }
  .credential-badge::after {
    content: ""; position: absolute; left: 107px; top: 10px;
    width: 64px; height: 64px; border-radius: 50%; background: var(--white);
  }

  .appointment {
    position: absolute; left: 345px; color: var(--ink-blue); font-size: 19px;
    display: flex; align-items: baseline; gap: 6px;
  }
  .appointment--date { top: 70px; }
  .appointment--time { top: 106px; }
  .appointment .dots { border-bottom: 2px dotted var(--ink-blue); display: inline-block; height: 12px; }
  .appointment--date .dots { width: 210px; }
  .appointment--time .dots { width: 145px; }
  .appointment .meridiem { font-size: 14px; }

  .notes-line { position: absolute; left: 41px; width: 646px; height: 1px; background: var(--rule); }
  .notes-line:nth-of-type(1) { top: 198px; }
  .notes-line:nth-of-type(2) { top: 240px; }
  .notes-line:nth-of-type(3) { top: 283px; }
  .notes-line:nth-of-type(4) { top: 326px; }

  .region-band {
    position: absolute; left: 0; bottom: 0; width: 100%; height: 64px;
    background: linear-gradient(90deg, var(--band-dark), var(--band-light) 50%, var(--band-dark));
    display: flex; flex-direction: column; justify-content: center; align-items: center;
  }
  .clinic-row {
    font-family: "Noto Serif", serif; font-size: 17px; line-height: 24px;
    color: var(--white); white-space: nowrap;
  }
  .clinic-sep { color: var(--accent-gold); padding: 0 8px; }
</style>
</head>
<body>
  <section class="card card--front">
    <svg class="front-art" viewBox="0 0 513 309" preserveAspectRatio="none" aria-hidden="true">
      <defs>
        <radialGradient id="front-blue" cx="0.35" cy="0.45" r="0.7">
          <stop offset="0" stop-color="#0a7cd0"/>
          <stop offset="1" stop-color="#1d2a8c"/>
        </radialGradient>
      </defs>
      <rect width="513" height="309" fill="url(#front-blue)"/>
      <circle cx="402" cy="155" r="167" fill="#8cc63f"/>
      <circle cx="402" cy="155" r="155" fill="#ffffff"/>
    </svg>

    <h1 class="holder-name">Marcus Kendrick</h1>
    <p class="holder-role">Nutritionist &amp; Chef</p>
    <ul class="contact-list">
      <li>0427 561 903</li>
      <li>6457 2183</li>
      <li>marcus.k.diet@fernmail.com</li>
      <li>brightfieldnutrition.com.au</li>
    </ul>

    <div class="brand">
      <span class="brand-dot"></span>
      <span class="brand-name">Brightfield</span>
    </div>
  </section>

  <section class="card card--back">
    <div class="credential-badge" role="img" aria-label="Certified Clinical Nutritionist badge"></div>

    <p class="appointment appointment--date">Date : <span class="dots"></span></p>
    <p class="appointment appointment--time">Time : <span class="dots"></span><span class="meridiem">AM/PM</span></p>

    <div class="notes">
      <div class="notes-line"></div>
      <div class="notes-line"></div>
      <div class="notes-line"></div>
      <div class="notes-line"></div>
    </div>

    <div class="region-band">
      <p class="clinic-row">Pinebrook Medical Centre<span class="clinic-sep">•</span>North Corrin Health</p>
      <p class="clinic-row">Hollis Medical<span class="clinic-sep">•</span>Ashcombe Doctors Surgery</p>
    </div>
  </section>
</body>
</html>
```